Campaign: « Hellere Wege entdecken », « Discover brighter paths »

We would like to start a campaign for which we need a good visual appearance. So it's about creating a key visual that represents the activities around the campaign. The campaign « Hellere Wege entdecken » in english « Discover brighter paths » aims to make a valuable contribution to social integration and to counteract social isolation. More in the briefing.

Target Market(s)

Switzerland, Berne

Industry/Entity Type

Non Profit, NGO

Font styles to use
Sans Serif
Other font styles liked:
• Helvetica neue

Colors

Designer to choose colors to be used in the design.

```html
<!DOCTYPE html>
<html lang="de">
<head>
<meta charset="utf-8">
<title>Hellere Wege entdecken – Key Visual</title>
<link href="https://fonts.googleapis.com/css2?family=Roboto+Condensed:wght@900&family=Poppins:wght@500&display=swap" rel="stylesheet">
<style>
  :root {
    --canvas: #d6d6d6;
    --ink: #222222;
    --white: #ffffff;
    --red: #e0001a;
    --blue: #5f88a8;
    --green: #9ab52c;
    --night: #0e0e0e;
  }
  * { margin: 0; padding: 0; box-sizing: border-box; }
  html, body { width: 1200px; height: 1200px; overflow: hidden; background: var(--canvas); }
  .grid { position: relative; width: 1200px; height: 1200px; }
  .tile {
    position: absolute; overflow: hidden;
    box-shadow: 0 4px 14px rgba(0,0,0,.28);
  }
  .tile--outdoor { left: 0; top: 0; width: 593px; height: 590px; background: var(--white); }
  .tile--terrace { left: 614px; top: 0; width: 586px; height: 590px; background: #2a1c12; }
  .tile--concert { left: 0; top: 606px; width: 593px; height: 594px; background: #0c1222; }
  .tile--brand { left: 614px; top: 606px; width: 586px; height: 594px; background: var(--night); }

  .photo { position: absolute; inset: 0; }
  .photo--hikers {
    background:
      linear-gradient(180deg, rgba(255,255,255,0) 40%, rgba(255,255,255,.85) 78%, #fff 88%),
      linear-gradient(180deg, #eeeeee 0%, #e4e4e4 30%, #b9b6ad 50%, #8f8a80 70%, #c9c7c2 100%);
  }
  .photo--terrace {
    background:
      linear-gradient(180deg, rgba(0,0,0,0) 55%, rgba(0,0,0,.85) 100%),
      radial-gradient(ellipse at 30% 10%, #e9773a 0%, rgba(233,119,58,0) 35%),
      linear-gradient(135deg, #7a5a2c 0%, #5e3a22 35%, #3b2617 65%, #15100b 100%);
  }
  .photo--concert {
    background:
      radial-gradient(ellipse at 70% 55%, #8a3b22 0%, rgba(138,59,34,0) 40%),
      radial-gradient(ellipse at 30% 70%, #5a3324 0%, rgba(90,51,36,0) 45%),
      linear-gradient(160deg, #0e1630 0%, #2a1530 45%, #3a1a1e 75%, #1d1d2a 100%);
  }

  .headline {
    position: absolute; left: 112px; width: 368px;
    font-family: "Roboto Condensed", "Arial Narrow", sans-serif;
    font-weight: 900; text-align: center;
  }
  .headline__main { font-size: 60px; line-height: 1; letter-spacing: -0.5px; }
  .headline__band {
    display: block; margin-top: 6px; height: 57px;
    font-size: 40px; line-height: 57px; color: var(--white);
  }
  .tile--outdoor .headline { top: 408px; }
  .tile--outdoor .headline__main { color: var(--ink); }
  .tile--outdoor .headline__band { background: var(--red); font-size: 46px; }
  .tile--terrace .headline { top: 235px; }
  .tile--terrace .headline__main { color: var(--white); }
  .tile--terrace .headline__band { background: rgba(95,136,168,.85); }
  .tile--concert .headline { top: 423px; }
  .tile--concert .headline__main { color: var(--white); }
  .tile--concert .headline__band { background: rgba(154,181,44,.88); }

  .wordmark {
    position: absolute; display: flex; align-items: center; gap: 10px;
    font-family: "Poppins", "Helvetica Neue", Arial, sans-serif; font-weight: 500;
    text-transform: uppercase; white-space: nowrap;
  }
  .wordmark__dot { border-radius: 50%; flex: none; }
  .wordmark__name { line-height: 1.05; }
  .tile--outdoor .wordmark { top: 44px; left: 147px; font-size: 22px; color: var(--ink); }
  .tile--outdoor .wordmark__dot { width: 62px; height: 62px; border: 5px solid var(--ink); }
  .tile--terrace .wordmark { top: 496px; left: 200px; font-size: 16px; color: var(--white); }
  .tile--terrace .wordmark__dot { width: 48px; height: 48px; border: 4px solid var(--white); }
  .tile--concert .wordmark { top: 50px; left: 219px; font-size: 15px; color: var(--white); }
  .tile--concert .wordmark__dot { width: 44px; height: 44px; border: 4px solid var(--white); }

  .brand-lockup {
    position: absolute; left: 0; right: 0; top: 196px;
    display: flex; flex-direction: column; align-items: center; gap: 26px;
    font-family: "Poppins", "Helvetica Neue", Arial, sans-serif; font-weight: 500;
    color: var(--white); text-transform: uppercase; text-align: center;
  }
  .brand-lockup__dot { width: 108px; height: 108px; border-radius: 50%; border: 7px solid var(--white); }
  .brand-lockup__name { font-size: 38px; line-height: 1.15; letter-spacing: 1px; }
</style>
</head>
<body>
<main class="grid">
  <section class="tile tile--outdoor">
    <div class="photo photo--hikers" role="img" aria-label="Drei junge Menschen mit Rucksäcken blicken von hinten gesehen in eine neblige Landschaft"></div>
    <div class="wordmark"><span class="wordmark__dot"></span><span class="wordmark__name">Hellere Wege<br>entdecken</span></div>
    <h1 class="headline"><span class="headline__main">Hellere Wege</span><span class="headline__band">entdecken</span></h1>
  </section>

  <section class="tile tile--terrace">
    <div class="photo photo--terrace" role="img" aria-label="Freundesgruppe lacht gemeinsam an einem Tisch auf einer sonnigen Restaurantterrasse"></div>
    <h2 class="headline"><span class="headline__main">Hellere Wege</span><span class="headline__band">entdecken</span></h2>
    <div class="wordmark"><span class="wordmark__dot"></span><span class="wordmark__name">Hellere Wege<br>entdecken</span></div>
  </section>

  <section class="tile tile--concert">
    <div class="photo photo--concert" role="img" aria-label="Zwei junge Menschen lachen begeistert bei einem Konzert im bunten Bühnenlicht"></div>
    <div class="wordmark"><span class="wordmark__dot"></span><span class="wordmark__name">Hellere Wege<br>entdecken</span></div>
    <h2 class="headline"><span class="headline__main">Hellere Wege</span><span class="headline__band">entdecken</span></h2>
  </section>

  <section class="tile tile--brand">
    <div class="brand-lockup">
      <span class="brand-lockup__dot"></span>
      <span class="brand-lockup__name">Hellere Wege<br>entdecken</span>
    </div>
  </section>
</main>
</body>
</html>
```